Bref créative
Dale's Homewares
Stationary, Letterhead, Business Cards, Envelopes
I need single sided standard sized Business Card [3.5" x 2"]
Similar to Logo Font
Bright & Fun-filled
Dale's Homewares and Gadgets
4817 W. Pinecrest Blvd.
Chicago IL 60691
Daleshomewaresandgadgets@mailbox-example.com
www.daleshomewaresandgadgts.example
Current Logo
Black and White Version

```html
<!DOCTYPE html>
<html lang="en">
<head>
<meta charset="utf-8">
<title>Dale's Homewares – Stationery Set</title>
<link href="https://fonts.googleapis.com/css2?family=Cinzel:wght@700&family=Open+Sans:wght@400;600&display=swap" rel="stylesheet">
<style>
  :root{
    --bg:#8a8a8a;
    --paper:#ffffff;
    --ink:#2b2b2b;
    --muted:#6b6b6b;
    --red:#d10a0a;
    --red-dark:#6e0000;
    --shadow:rgba(0,0,0,.35);
  }
  *{margin:0;padding:0;box-sizing:border-box}
  html,body{width:1200px;height:797px;overflow:hidden}
  body{background:var(--bg);position:relative;font-family:"Open Sans",Arial,sans-serif;color:var(--ink)}
  .sheet{position:absolute;background:var(--paper);box-shadow:2px 3px 8px var(--shadow);overflow:hidden}

  .brand{position:absolute;display:flex;align-items:center;gap:6px}
  .brand__mark{background:var(--red);flex:none}
  .brand__name{font-family:"Cinzel",Georgia,serif;font-weight:700;color:var(--ink);white-space:nowrap;line-height:1}

  .contact{position:absolute;font-size:7px;line-height:1.45;color:var(--muted)}
  .contact .phone{color:var(--red)}
  .red-band{position:absolute;left:0;right:0;bottom:0;background:linear-gradient(90deg,#fff 0%,var(--red) 55%,var(--red-dark) 100%)}

  /* letterhead */
  .letterhead{left:67px;top:101px;width:492px;height:638px}
  .letterhead .brand{left:44px;top:46px}
  .letterhead .brand__mark{width:14px;height:14px}
  .letterhead .brand__name{font-size:19px}
  .letterhead .contact{right:18px;top:48px;text-align:right;font-size:6.5px}
  .letterhead .red-band{height:14px;bottom:6px}
  .letterhead .foot-brand{right:12px;bottom:22px}
  .letterhead .foot-brand .brand__mark{width:7px;height:7px}
  .letterhead .foot-brand .brand__name{font-size:10px}

  /* business cards */
  .card{top:101px;width:200px;height:115px;border-radius:6px}
  .card--primary{left:600px}
  .card--secondary{left:830px}
  .card .brand{left:12px;top:14px;gap:4px}
  .card .brand__mark{width:7px;height:7px}
  .card .brand__name{font-size:9.5px}
  .card .person{position:absolute;right:12px;top:14px;text-align:right;font-size:7px;font-weight:600;color:var(--red)}
  .card .person span{display:block;font-weight:400;color:var(--muted);font-size:6px}
  .card .contact{left:12px;top:42px;font-size:5.5px}
  .card .red-band{height:12px;display:flex;align-items:center;justify-content:center;font-size:5px;color:#fff;letter-spacing:.3px}

  /* envelope back */
  .envelope-back{left:576px;top:245px;width:557px;height:240px}
  .envelope-back svg{position:absolute;left:0;top:0}
  .envelope-back .flap-web{position:absolute;left:0;right:0;top:24px;text-align:center;font-size:6px;color:#fff;letter-spacing:.3px}

  /* envelope front */
  .envelope-front{left:576px;top:499px;width:557px;height:240px}
  .envelope-front .brand{left:30px;top:28px}
  .envelope-front .brand__mark{width:11px;height:11px}
  .envelope-front .brand__name{font-size:15px}
  .envelope-front .contact{left:30px;top:60px;font-size:6.5px}
  .envelope-front .window{position:absolute;left:276px;top:115px;width:247px;height:75px;border-radius:8px;background:#e6e6e6;border:1px solid #d3d3d3}
  .envelope-front .red-band{height:12px;bottom:6px}
  .envelope-front .foot-brand{right:14px;bottom:20px}
  .envelope-front .foot-brand .brand__mark{width:7px;height:7px}
  .envelope-front .foot-brand .brand__name{font-size:10px}
</style>
</head>
<body>

<section class="sheet letterhead">
  <div class="brand"><span class="brand__mark"></span><span class="brand__name">Dale's Homewares</span></div>
  <div class="contact">
    4817 W. Pinecrest Blvd. Chicago IL 60691<br>
    <span class="phone">Ph: 773-555-0142 Fax: 773-555-0198</span><br>
    www.daleshomewaresandgadgts.example
  </div>
  <div class="brand foot-brand"><span class="brand__mark"></span><span class="brand__name">Dale's Homewares</span></div>
  <div class="red-band"></div>
</section>

<section class="sheet card card--primary">
  <div class="brand"><span class="brand__mark"></span><span class="brand__name">Dale's Homewares</span></div>
  <div class="person">Dale Morrow<span>Store Manager</span></div>
  <div class="contact">
    4817 W. Pinecrest Blvd.<br>
    Chicago IL 60691<br>
    <span class="phone">Ph: 773-555-0142 Fax: 773-555-0198</span><br>
    Daleshomewaresandgadgets@mailbox-example.com
  </div>
  <div class="red-band">www.daleshomewaresandgadgts.example</div>
</section>

<section class="sheet card card--secondary">
  <div class="brand"><span class="brand__mark"></span><span class="brand__name">Dale's Homewares</span></div>
  <div class="person">Ann Morrow<span>Sales Manager</span></div>
  <div class="contact">
    4817 W. Pinecrest Blvd.<br>
    Chicago IL 60691<br>
    <span class="phone">Ph: 773-555-0142 Fax: 773-555-0198</span><br>
    Daleshomewaresandgadgets@mailbox-example.com
  </div>
  <div class="red-band">www.daleshomewaresandgadgts.example</div>
</section>

<section class="sheet envelope-back">
  <svg width="557" height="240" viewBox="0 0 557 240" aria-hidden="true">
    <defs>
      <radialGradient id="flapFill" cx="50%" cy="30%" r="70%">
        <stop offset="0" stop-color="#ff1a1a"/>
        <stop offset=".6" stop-color="#c00000"/>
        <stop offset="1" stop-color="#3a0000"/>
      </radialGradient>
    </defs>
    <path d="M0 0 H557 C470 70 360 125 278 152 C196 125 87 70 0 0 Z" fill="url(#flapFill)"/>
    <path d="M0 0 C87 70 196 125 278 152 C360 125 470 70 557 0" fill="none" stroke="#e3e3e3" stroke-width="1.5"/>
  </svg>
  <div class="flap-web">www.daleshomewaresandgadgts.example</div>
</section>

<section class="sheet envelope-front">
  <div class="brand"><span class="brand__mark"></span><span class="brand__name">Dale's Homewares</span></div>
  <div class="contact">
    4817 W. Pinecrest Blvd. Chicago IL 60691<br>
    <span class="phone">Ph: 773-555-0142 Fax: 773-555-0198</span>
  </div>
  <div class="window"></div>
  <div class="brand foot-brand"><span class="brand__mark"></span><span class="brand__name">Dale's Homewares</span></div>
  <div class="red-band"></div>
</section>

</body>
</html>
```